VL - menu design

Hi,

We require elegant menu design for upscale restaurant. Please find attached the logo and the menu items for your reference.

for inspiration, this is a good website: -
http://www.plateworthy-sample.net/dishcraft/about.php

We are very much open for Menu Size suggestions.

unfortunately the place is going under renovation, we don't have updated images to it. the closest look and feel to our place is http://vazelo-example.com ..

we are also open for creative options on the shape, the styles, etc. as long as it represents the fine dine feel ...

Thanks ...

Dear All,

We wouldlike to extend our apology for not being able to provide feedbacks on everysingle design. We were extremely busy and we have multiple contests opensimultaneously which makes the process even harder.

However,we would like to thank you all for the efforts you have put into designingour menu. It is very much appreciated …

We wishyou all success in your design ventures and we are quite positive that we willbe working with many of you on many projects in the soon future. 

Thanks & Regards,

DQI Team...

 

 

 

Industry/Entity Type

Restaurant

Requirements
Must have
• Please ensure that there are 'some' images in the menu ... this is very important.
Should not have
• IMPORTANT: -

1. Please DO NOT insert any currency sign to the menu
2. Please keep the prices of the menu at the end of the menu items descriptions NOT beside the menu item names. The font of the price should be similar to the menu item description and please DO NOT bold the numbers. the prices should be subtle.

Thank you ...

```html
<!DOCTYPE html>
<html lang="en">
<head>
<meta charset="utf-8">
<title>VL – Breakfast &amp; Sandwiches Menu</title>
<link rel="stylesheet" href="https://fonts.googleapis.com/css2?family=Questrial&family=Didact+Gothic&display=swap">
<style>
  :root {
    --paper: #ffffff;
    --espresso: #3b2c22;
    --espresso-deep: #2e221b;
    --title-brown: #7b5a3d;
    --title-tan: #c9a47a;
    --ink: #2b2b2b;
    --ink-soft: #3a3a3a;
    --cream: #f6efe4;
  }
  * { margin: 0; padding: 0; box-sizing: border-box; }
  html, body { width: 1200px; height: 720px; overflow: hidden; background: var(--paper); }
  .menu-spread { position: relative; width: 1200px; height: 720px; font-family: "Didact Gothic", sans-serif; color: var(--ink); }

  .page { position: absolute; top: 0; height: 720px; width: 600px; }
  .page--breakfast { left: 0; background: var(--paper); }
  .page--sandwiches { left: 600px; background: var(--espresso); }

  .photo { position: absolute; }
  .photo--breakfast {
    left: 0; top: 0; width: 600px; height: 235px;
    background: linear-gradient(120deg, #e9dccb 0%, #d9b98c 30%, #f0a640 45%, #c98a4c 60%, #efe6da 100%);
  }
  .photo--sandwich {
    left: 0; top: 235px; width: 600px; height: 485px;
    background: radial-gradient(ellipse at 62% 48%, #c98a4a 0%, #9a5f2e 30%, #5e3a20 62%, #2f1e14 100%);
  }

  .ornament { position: absolute; height: 44px; }
  .ornament--breakfast { left: 305px; top: 200px; width: 245px;
    background: linear-gradient(90deg, rgba(123,90,61,0.55), rgba(123,90,61,0)); height: 4px; top: 224px; }
  .ornament--sandwiches { left: 20px; top: 262px; width: 248px;
    background: linear-gradient(90deg, rgba(240,225,205,0), rgba(240,225,205,0.6)); height: 4px; }

  .section-title { position: absolute; font-family: "Questrial", sans-serif; font-weight: 400; font-size: 37px; line-height: 1; padding: 8px 12px 7px; }
  .section-title--breakfast { left: 45px; top: 190px; width: 260px; background: var(--paper); color: var(--title-brown); }
  .section-title--sandwiches { left: 268px; top: 237px; width: 292px; background: var(--espresso-deep); color: var(--title-tan); }

  .dish-list { position: absolute; list-style: none; }
  .dish-list--breakfast { left: 58px; top: 246px; width: 500px; }
  .dish-list--sandwiches { left: 63px; top: 40px; width: 490px; color: #fff; }

  .dish--breakfast { margin-bottom: 6px; }
  .dish-name { font-family: "Questrial", sans-serif; font-size: 16.5px; font-weight: 400; line-height: 20px; color: var(--ink); }
  .dish-desc { font-size: 10.5px; line-height: 13px; color: var(--ink-soft); margin-top: 6px; }
  .dish-desc + .dish-desc { margin-top: 7px; }
  .dish--breakfast .dish-desc.tight { margin-top: 0; }

  .dish--sandwich { margin-bottom: 7px; font-size: 10.5px; line-height: 14px; color: #f3ece4; }
  .dish--sandwich .dish-name { display: inline; color: #fff; font-size: 16.5px; line-height: 20px; }

  .footer-band { position: absolute; left: 55px; bottom: 0; width: 545px; height: 17px; background: var(--espresso-deep); }
</style>
</head>
<body>
<main class="menu-spread">
  <section class="page page--breakfast">
    <div class="photo photo--breakfast" role="img" aria-label="Breakfast table with coffee cup, orange juice, oranges, apple, croissant and toast"></div>
    <div class="ornament ornament--breakfast" role="img" aria-label="Decorative flourish"></div>
    <h2 class="section-title section-title--breakfast">The Breakfast</h2>
    <ul class="dish-list dish-list--breakfast">
      <li class="dish dish--breakfast">
        <h3 class="dish-name">Butter Croisasant</h3>
        <p class="dish-desc">Served plain with a selection of two jams, a vanilla custard cream, a chocolate Cream and butter curls). 36</p>
      </li>
      <li class="dish dish--breakfast">
        <h3 class="dish-name">Cheese Croissant</h3>
        <p class="dish-desc">Crumbly freshly baked with cheese filling. 29</p>
      </li>
      <li class="dish dish--breakfast">
        <h3 class="dish-name">Daily Fresh Eggs</h3>
        <p class="dish-desc">A choice of poached, scrambled, pan fried, omelet) all served with toasted</p>
        <p class="dish-desc">Bread, mushrooms, roasted tomatoes and chicken sausages. 59</p>
      </li>
      <li class="dish dish--breakfast">
        <h3 class="dish-name">Healthy Time</h3>
        <p class="dish-desc">One choice of hot beverage from our cafe served with fruit salad, natural</p>
        <p class="dish-desc">Yoghurt, whole wheat bread vegetable sandwiches and sugar free biscuits selection.49</p>
      </li>
      <li class="dish dish--breakfast">
        <h3 class="dish-name">Energy Time</h3>
        <p class="dish-desc">One choice of hot beverage from our cafe served with finger chocolate muffins,</p>
        <p class="dish-desc">Poached egg with toasted bread and crispy beef bacon, crepe roll with goat</p>
        <p class="dish-desc">Cheese and honey and finger chocolate cream with salted cookies.</p>
      </li>
      <li class="dish dish--breakfast">
        <h3 class="dish-name">Third Avenue Time</h3>
        <p class="dish-desc">One choice of hot beverage from our cafe served with our selection of scones, Smoked salmon and avocado sandwich, roasted sausages sandwich, grilled vegetables sandwich, selection of our best biscuits. 59</p>
      </li>
      <li class="dish dish--breakfast">
        <h3 class="dish-name">The Arabic Breakfast</h3>
        <p class="dish-desc">Choice of Zattar Manakish and Cheese Manakish, served with one choice of hot beverage from our cafe and fresh orange juice. 59</p>
      </li>
    </ul>
    <div class="footer-band"></div>
  </section>

  <section class="page page--sandwiches">
    <ul class="dish-list dish-list--sandwiches">
      <li class="dish dish--sandwich"><h3 class="dish-name">Grilled Vegetables Sandwich</h3> with fresh Goat cheese and chives served with our Homemade spicy garlic mayo. 59</li>
      <li class="dish dish--sandwich"><h3 class="dish-name">Butterfish burger</h3> with fresh tomato, beef bacon, grilled vegetables and béarnaise sauce. Tataki Tuna sandwich with red onion slices, stewed endives and black olives and sultanas pate’. 79</li>
      <li class="dish dish--sandwich"><h3 class="dish-name">Beef sirloin steak sandwich</h3> with grain mustard, Parmesan cheese and fresh Nashi pears. 79</li>
      <li class="dish dish--sandwich"><h3 class="dish-name">The Traditional Club sandwich</h3> served with French fries and vegetable chips. 69</li>
      <li class="dish dish--sandwich"><h3 class="dish-name">Chicken sandwich</h3> with Parmesan cheese slices, sundried tomatoes and mint Flavored mayo. 69</li>
    </ul>
    <div class="photo photo--sandwich" role="img" aria-label="Toasted bacon, lettuce and tomato sandwich on a brown napkin"></div>
    <div class="ornament ornament--sandwiches" role="img" aria-label="Decorative flourish"></div>
    <h2 class="section-title section-title--sandwiches">The Sandwiches</h2>
  </section>
</main>
</body>
</html>
```